product development company BRVEMKO LLC business card

We need a business card design for a company based in Texas called 'BRVEMKO LLC'. Our first product is a illuminated portable ice chest that is called ' Copper Harbor coolers'. Copper harbor coolers is trademarked. I would like to have the copper harbor trademark somewhere on the card as well as the BRVEMKO LLC name.

Target Market(s)

outdoor industry

Industry/Entity Type

Business

Contact Information for Business Card

i would like to have BRVEMKO LLC logo larger than the Copper harbor coolers logo.

Font styles to use
Serif
Sans Serif

```html
<!DOCTYPE html>
<html lang="en">
<head>
<meta charset="utf-8">
<title>BRVEMKO LLC business card</title>
<link href="https://fonts.googleapis.com/css2?family=Marcellus&family=Roboto:wght@400;700&display=swap" rel="stylesheet">
<style>
  :root {
    --backdrop: #e4dfdc;
    --card-dark: #000000;
    --card-light: #ffffff;
    --ink: #111111;
    --ink-reverse: #ffffff;
    --dots: #333333;
    --faint: #ebebec;
  }
  * { margin: 0; padding: 0; box-sizing: border-box; }
  html, body { width: 1200px; height: 1000px; overflow: hidden; }
  body { background: var(--backdrop); font-family: "Roboto", Arial, sans-serif; position: relative; }

  .card { position: absolute; left: 287px; width: 626px; height: 358px; border-radius: 22px; overflow: hidden; }
  .card-front { top: 132px; background: var(--card-dark); color: var(--ink-reverse); }
  .card-back { top: 520px; background: var(--card-light); color: var(--ink); }

  .company-name { position: absolute; font-family: "Marcellus", Georgia, serif; font-weight: 400; line-height: 1; white-space: nowrap; }
  .card-front .company-name { left: 0; right: 0; top: 155px; text-align: center; font-size: 54px; color: var(--ink-reverse); }
  .card-back .company-name { left: 28px; top: 42px; font-size: 31px; color: var(--ink); }

  .backdrop-shape { position: absolute; left: 55px; top: 0; width: 250px; height: 358px; background: var(--faint); }

  .person { position: absolute; right: 27px; top: 42px; text-align: right; }
  .person-name { font-weight: 700; font-size: 21px; font-variant: small-caps; letter-spacing: .5px; }
  .person-title { font-size: 15px; letter-spacing: 2px; margin-top: 2px; }

  .product-mark { position: absolute; right: 38px; top: 202px; display: flex; align-items: center; gap: 5px; font-weight: 700; font-size: 11px; color: var(--ink); }
  .product-mark-square { width: 14px; height: 14px; background: var(--ink); }

  .divider { position: absolute; left: 18px; right: 16px; top: 251px; border-top: 2.5px dotted var(--dots); }

  .contact-band { position: absolute; left: 0; right: 0; top: 254px; bottom: 0; background: var(--card-light); }
  .contact { position: absolute; top: 274px; font-size: 16px; line-height: 20.5px; }
  .contact-left { left: 34px; }
  .contact-right { left: 236px; }
  .contact-line { display: flex; align-items: flex-start; gap: 6px; }
  .contact-line svg { width: 15px; height: 15px; margin-top: 3px; flex: none; fill: var(--ink); }
  .contact-line .no-icon { width: 15px; flex: none; }
  .contact-strong { font-weight: 700; }
</style>
</head>
<body>

<section class="card card-front" aria-label="Card front">
  <div class="company-name">BRVEMKO LLC</div>
</section>

<section class="card card-back" aria-label="Card back">
  <div class="backdrop-shape" role="img" aria-label="Faint product mark background area"></div>

  <div class="company-name">BRVEMKO LLC</div>

  <div class="person">
    <div class="person-name">M. Dalton Reyes</div>
    <div class="person-title">DIRECTOR</div>
  </div>

  <div class="product-mark">
    <span class="product-mark-square"></span>
    <span>Copper Harbor coolers</span>
  </div>

  <div class="divider"></div>

  <div class="contact contact-left">
    <div class="contact-line">
      <svg viewBox="0 0 16 16"><path d="M1 5c0-2 3-3 7-3s7 1 7 3v1h-4V5H5v1H1z"/><path d="M3 8l2-2h6l2 2v6H3z M6 9v3h4V9z"/></svg>
      <span>123 456 7890</span>
    </div>
    <div class="contact-line">
      <svg viewBox="0 0 16 16"><path d="M4 0h8a1 1 0 0 1 1 1v14a1 1 0 0 1-1 1H4a1 1 0 0 1-1-1V1a1 1 0 0 1 1-1zm1 2v10h6V2zm3 11a1 1 0 1 0 0 2 1 1 0 0 0 0-2z"/></svg>
      <span>123 456 7890</span>
    </div>
    <div class="contact-line">
      <svg viewBox="0 0 16 16"><path d="M0 3h16v10H0zm1.5 1.2V12h13V4.2L8 9z"/></svg>
      <span>BRVEMKO@info.com</span>
    </div>
  </div>

  <div class="contact contact-right">
    <div class="contact-line">
      <svg viewBox="0 0 16 16"><path d="M8 1a7 7 0 1 0 0 14A7 7 0 0 0 8 1zm0 1.5c.8 0 1.7 1.5 2 4H6c.3-2.5 1.2-4 2-4zM2.6 7h2.5c0 .7 0 1.4.1 2H2.6a5.5 5.5 0 0 1 0-2zm8.3 0h2.5a5.5 5.5 0 0 1 0 2h-2.6c.1-.6.1-1.3.1-2zM6 9.5h4c-.3 2.5-1.2 4-2 4s-1.7-1.5-2-4z"/></svg>
      <span>www.BRVEMKO.com</span>
    </div>
    <div class="contact-line">
      <svg viewBox="0 0 16 16"><path d="M8 0a5 5 0 0 0-5 5c0 4 5 9 5 9s5-5 5-9a5 5 0 0 0-5-5zm0 3a2 2 0 1 1 0 4 2 2 0 0 1 0-4z"/><rect x="4" y="15" width="8" height="1"/></svg>
      <span class="contact-strong">BRVEMKO LLC</span>
    </div>
    <div class="contact-line">
      <span class="no-icon"></span>
      <span>1450 Mesquite Ave. Arlington</span>
    </div>
  </div>
</section>

</body>
</html>
```